Harrow Grading LLC business card design

Excavation company business cards

Contact Information for Business Card

Harrow Grading LLC cell phone 208-417-6290 office phone 208-319-4856 harrowgradingllc@maplecove.com Driveways, site prep, retaining walls, septic systems, rock delivery

Colors

Designer to choose colors to be used in the design.

```html
<!DOCTYPE html>
<html lang="en">
<head>
<meta charset="utf-8">
<title>Harrow Grading LLC – Business Card</title>
<link href="https://fonts.googleapis.com/css2?family=Montserrat:wght@400;500;700;800&display=swap" rel="stylesheet">
<style>
  :root {
    --bg: #e4e4e6;
    --card-dark: #1e1e1f;
    --card-light: #ffffff;
    --orange: #ef6a1f;
    --ink: #4a4a4c;
    --white: #ffffff;
  }
  html, body {
    margin: 0;
    width: 1200px;
    height: 912px;
    overflow: hidden;
    background: var(--bg);
    font-family: "Montserrat", sans-serif;
  }
  .stage {
    position: relative;
    width: 1200px;
    height: 912px;
  }
  .card {
    position: absolute;
    left: 267px;
    width: 665px;
    height: 380px;
    box-shadow: 0 10px 28px rgba(0,0,0,0.18);
    box-sizing: border-box;
  }
  .card-front {
    top: 56px;
    background: var(--card-dark);
    display: flex;
    align-items: center;
    justify-content: center;
  }
  .card-back {
    top: 476px;
    background: var(--card-light);
    color: var(--ink);
  }
  .brand {
    display: flex;
    align-items: center;
    gap: 14px;
    font-weight: 800;
    color: var(--orange);
    letter-spacing: 0.02em;
    text-transform: uppercase;
  }
  .brand-mark {
    background: var(--orange);
    flex: none;
  }
  .card-front .brand { font-size: 40px; }
  .card-front .brand-mark { width: 34px; height: 34px; }
  .card-back .brand {
    position: absolute;
    top: 48px;
    left: 0;
    right: 0;
    justify-content: center;
    font-size: 28px;
  }
  .card-back .brand-mark { width: 24px; height: 24px; }
  .contact-block {
    position: absolute;
    top: 150px;
    left: 0;
    right: 0;
    display: flex;
    justify-content: center;
    align-items: center;
    gap: 26px;
  }
  .person { text-align: right; }
  .person-name {
    color: var(--orange);
    font-weight: 700;
    font-size: 24px;
    margin: 0;
  }
  .person-role {
    font-size: 19px;
    margin: 4px 0 0;
    color: var(--ink);
  }
  .divider {
    width: 2px;
    height: 96px;
    background: var(--orange);
  }
  .contact-list {
    list-style: none;
    margin: 0;
    padding: 0;
    font-size: 17px;
    line-height: 1.55;
  }
  .contact-list li {
    display: flex;
    align-items: center;
    gap: 10px;
  }
  .contact-list svg { width: 13px; height: 13px; flex: none; }
  .services {
    position: absolute;
    bottom: 44px;
    left: 0;
    right: 0;
    text-align: center;
    font-size: 17px;
    color: var(--ink);
  }
  .services .sep {
    color: var(--orange);
    font-weight: 700;
    margin: 0 6px;
  }
</style>
</head>
<body>
<main class="stage">
  <section class="card card-front" aria-label="Card front">
    <div class="brand"><span class="brand-mark"></span>Harrow Grading LLC</div>
  </section>

  <section class="card card-back" aria-label="Card back">
    <div class="brand"><span class="brand-mark"></span>Harrow Grading LLC</div>

    <div class="contact-block">
      <div class="person">
        <p class="person-name">DALE MORRISON</p>
        <p class="person-role">Director</p>
      </div>
      <div class="divider"></div>
      <ul class="contact-list">
        <li>
          <svg viewBox="0 0 12 12" aria-hidden="true"><rect x="3" y="0.8" width="6" height="10.4" rx="1.2" fill="none" stroke="#ef6a1f" stroke-width="1.4"/></svg>
          208-417-6290
        </li>
        <li>
          <svg viewBox="0 0 12 12" aria-hidden="true"><path d="M1 4 Q6 0 11 4 L9.5 5.5 L8 4.5 L4 4.5 L2.5 5.5 Z M2.5 6.5 H9.5 L10.5 11 H1.5 Z" fill="#ef6a1f"/></svg>
          208-319-4856
        </li>
        <li>
          <svg viewBox="0 0 12 12" aria-hidden="true"><rect x="0.8" y="2.3" width="10.4" height="7.4" fill="none" stroke="#ef6a1f" stroke-width="1.3"/><path d="M0.8 2.5 L6 6.5 L11.2 2.5" fill="none" stroke="#ef6a1f" stroke-width="1.3"/></svg>
          harrowgradingllc@maplecove.com
        </li>
      </ul>
    </div>

    <p class="services">Driveways,<span class="sep">|</span>site prep,<span class="sep">|</span>retaining walls,<span class="sep">|</span>septic systems,<span class="sep">|</span>rock delivery</p>
  </section>
</main>
</body>
</html>
```